Copper Lantern

Need a business card for our restaurant. Restaurant and Bar in the mountains of North Idaho. Rustic looking card

rustic design, wood and metal looking, primarily neutral colors

• Name, address, phone number, website, email address

```html
<!DOCTYPE html>
<html lang="en">
<head>
<meta charset="UTF-8">
<title>Copper Lantern – Business Card</title>
<link href="https://fonts.googleapis.com/css2?family=Lato:wght@400;700&family=Permanent+Marker&display=swap" rel="stylesheet">
<style>
  :root {
    --page: #2b2b2b;
    --card-white: #ffffff;
    --ink: #111111;
    --panel-dark: #0f0f0f;
    --panel-mid: #2a2a2a;
    --panel-light: #3a3a3a;
    --text-light: #f2f2f2;
    --text-muted: #d0d0d0;
    --pattern-tone: #ececec;
  }
  * { margin: 0; padding: 0; box-sizing: border-box; }
  html, body { width: 1200px; height: 875px; overflow: hidden; }
  body {
    background: var(--page);
    display: flex;
    flex-direction: column;
    align-items: center;
    justify-content: center;
    gap: 30px;
    font-family: 'Lato', sans-serif;
  }
  .card {
    position: relative;
    width: 700px;
    height: 400px;
    border-radius: 22px;
    overflow: hidden;
    background: var(--card-white);
  }

  /* Back side */
  .card-back .pattern-field {
    position: absolute;
    inset: 0;
    background:
      radial-gradient(ellipse at 30% 40%, var(--card-white) 0%, transparent 60%),
      repeating-linear-gradient(90deg, var(--card-white) 0 34px, var(--pattern-tone) 34px 56px),
      var(--card-white);
    opacity: 0.85;
  }
  .card-back .corner-name {
    position: absolute;
    right: 34px;
    top: 150px;
    display: flex;
    align-items: center;
    gap: 8px;
    font-size: 18px;
    font-weight: 700;
    color: var(--ink);
  }
  .card-back .corner-name .mark {
    width: 12px;
    height: 12px;
    border-radius: 50%;
    background: var(--ink);
  }

  /* Front side */
  .card-front .dark-panel {
    position: absolute;
    inset: 0;
  }
  .card-front .seal-name {
    position: absolute;
    left: 430px;
    top: 112px;
    width: 220px;
    text-align: center;
    font-size: 26px;
    font-weight: 700;
    line-height: 1.15;
    color: var(--ink);
    letter-spacing: 1px;
  }
  .card-front .seal-name .dot {
    display: block;
    width: 10px;
    height: 10px;
    border-radius: 50%;
    background: var(--ink);
    margin: 12px auto 0;
  }
  .contact-block {
    position: absolute;
    left: 48px;
    top: 168px;
    color: var(--text-light);
  }
  .person-name {
    font-family: 'Permanent Marker', 'Comic Sans MS', cursive;
    font-size: 30px;
    line-height: 38px;
    letter-spacing: 1.5px;
    color: var(--text-light);
  }
  .person-role {
    font-size: 17px;
    color: var(--text-muted);
    margin-top: 2px;
  }
  .divider {
    width: 68px;
    height: 1px;
    background: var(--text-muted);
    margin: 14px 0 12px;
  }
  .contact-list { list-style: none; }
  .contact-list li {
    display: flex;
    align-items: center;
    gap: 10px;
    font-size: 15px;
    line-height: 24px;
    color: var(--text-light);
  }
  .contact-list svg { width: 13px; height: 13px; flex: none; }
</style>
</head>
<body>

  <section class="card card-back" aria-label="Card back">
    <div class="pattern-field" role="img" aria-label="Faint repeating brand pattern across the card"></div>
    <div class="corner-name"><span class="mark"></span>Copper Lantern</div>
  </section>

  <section class="card card-front" aria-label="Card front">
    <svg class="dark-panel" viewBox="0 0 700 400" role="img" aria-label="Dark distressed slate texture behind the contact details">
      <defs>
        <radialGradient id="wornTone" cx="0.35" cy="0.55" r="0.8">
          <stop offset="0" stop-color="var(--panel-light)"/>
          <stop offset="0.45" stop-color="var(--panel-mid)"/>
          <stop offset="1" stop-color="var(--panel-dark)"/>
        </radialGradient>
        <mask id="sealCut">
          <rect width="700" height="400" fill="#fff"/>
          <circle cx="540" cy="140" r="196" fill="#000"/>
        </mask>
      </defs>
      <rect x="14" y="14" width="672" height="372" rx="16" fill="url(#wornTone)" mask="url(#sealCut)"/>
      <circle cx="540" cy="140" r="186" fill="none" stroke="var(--ink)" stroke-width="4"/>
    </svg>

    <div class="seal-name">Copper Lantern<span class="dot"></span></div>

    <div class="contact-block">
      <div class="person-name">DANIEL REED</div>
      <div class="person-role">Founder &amp; CEO</div>
      <div class="divider"></div>
      <ul class="contact-list">
        <li>
          <svg viewBox="0 0 24 24"><path fill="#f2f2f2" d="M6.6 10.8a15 15 0 0 0 6.6 6.6l2.2-2.2c.3-.3.7-.4 1-.2 1.1.4 2.3.6 3.6.6.6 0 1 .4 1 1V20c0 .6-.4 1-1 1A17 17 0 0 1 3 4c0-.6.4-1 1-1h3.5c.6 0 1 .4 1 1 0 1.3.2 2.5.6 3.6.1.3 0 .7-.2 1z"/></svg>
          (208) 555-0147
        </li>
        <li>
          <svg viewBox="0 0 24 24"><rect x="2" y="5" width="20" height="14" rx="2" fill="#f2f2f2"/><path d="M3 6l9 7 9-7" stroke="#161616" stroke-width="2" fill="none"/></svg>
          info@copperlanternidaho.com
        </li>
        <li>
          <svg viewBox="0 0 24 24"><circle cx="12" cy="12" r="9" fill="none" stroke="#f2f2f2" stroke-width="2"/><path d="M3 12h18M12 3c3 3 3 15 0 18M12 3c-3 3-3 15 0 18" stroke="#f2f2f2" stroke-width="1.5" fill="none"/></svg>
          copperlanternidaho.com
        </li>
        <li>
          <svg viewBox="0 0 24 24"><path fill="#f2f2f2" d="M12 2a7 7 0 0 0-7 7c0 5 7 13 7 13s7-8 7-13a7 7 0 0 0-7-7zm0 9.5A2.5 2.5 0 1 1 12 6.5a2.5 2.5 0 0 1 0 5z"/></svg>
          214 Timber Ln, Ridgefork, ID 83800
        </li>
      </ul>
    </div>
  </section>

</body>
</html>
```